diamondscoutline.net - Social Media Branding

diamondscoutline.net --> Social Media Re-Branding & Graphics
Facebook: @dmndscoutline - Instagram: @diamondscoutline - Twitter: @dmndscoutline

Looking to find a good designer to help with my diamondscoutline.net social media sites!
- facebook banner
- twitter banner
- instagram template (square and banner size)
- Quote or Information Template
- Committed Template (uniformed) - see the ones I made (& i am no professional) at diamondscoutline.net/committed - needs to have diamondscoutline.net logo, room for: the committed school and the team the player plays on.

Also willing to pay extra for a graphic that is the "complete package" that detail all of the steps of the recruiting process detailed in diamondscoutline.net

Font styles to use
Sans Serif

Colors
ec1f27
fbee3e

```html
<!DOCTYPE html>
<html lang="en">
<head>
<meta charset="utf-8">
<title>Free Recruiting Seminar – diamondscoutline.net</title>
<link rel="stylesheet" href="https://fonts.googleapis.com/css2?family=Rajdhani:wght@700&family=Source+Sans+3:wght@600;700&display=swap">
<style>
  :root {
    --brand-red: #ec1f27;
    --brand-red-deep: #d8141c;
    --brand-pink: #f3a2a6;
    --brand-yellow: #fbee3e;
    --ink: #111111;
    --paper: #ffffff;
    --pill-line: #2b2b2b;
  }
  html, body {
    margin: 0;
    padding: 0;
    width: 1200px;
    height: 1200px;
    overflow: hidden;
    background: var(--paper);
  }
  .flyer {
    position: relative;
    width: 1200px;
    height: 1200px;
    overflow: hidden;
    background: var(--paper);
    font-family: "Source Sans 3", "Segoe UI", sans-serif;
  }
  .flyer__shapes {
    position: absolute;
    inset: 0;
    width: 1200px;
    height: 1200px;
  }
  .brand {
    position: absolute;
    left: 23px;
    top: 100px;
    width: 320px;
    padding-bottom: 10px;
    border-bottom: 3px solid var(--brand-red);
  }
  .brand__name {
    margin: 0;
    font-weight: 700;
    font-size: 33px;
    line-height: 1;
    color: var(--ink);
    letter-spacing: -0.2px;
  }
  .headline {
    position: absolute;
    left: 77px;
    top: 330px;
    margin: 0;
    font-family: "Rajdhani", "Arial Narrow", sans-serif;
    font-weight: 700;
    font-size: 76px;
    line-height: 86px;
    letter-spacing: 2px;
    color: var(--brand-yellow);
    text-shadow: 4px 5px 6px rgba(90, 0, 0, 0.55);
  }
  .headline span { display: block; }
  .event-time {
    position: absolute;
    left: 120px;
    top: 798px;
    margin: 0;
    font-weight: 700;
    font-size: 39px;
    line-height: 55px;
    color: var(--ink);
  }
  .event-time span { display: block; }
  .event-time .event-time__hour { padding-left: 30px; }
  .audience {
    position: absolute;
    left: 600px;
    top: 772px;
    margin: 0;
    font-weight: 600;
    font-size: 39px;
    color: var(--ink);
    text-shadow: 2px 4px 6px rgba(236, 31, 39, 0.35);
  }
  .web-pill {
    position: absolute;
    left: 211px;
    top: 993px;
    width: 802px;
    height: 88px;
    box-sizing: border-box;
    border: 1.5px solid var(--pill-line);
    border-radius: 30px;
    background: var(--paper);
    box-shadow: 0 16px 12px -10px rgba(0, 0, 0, 0.35);
    display: flex;
    align-items: center;
    justify-content: center;
    gap: 18px;
  }
  .web-pill__icon { width: 46px; height: 46px; }
  .web-pill__url {
    font-weight: 700;
    font-size: 41px;
    color: var(--brand-red);
  }
  .social-bar {
    position: absolute;
    left: 0;
    top: 1140px;
    width: 1200px;
    height: 60px;
    background: var(--brand-red);
    display: flex;
    align-items: center;
    justify-content: center;
    gap: 32px;
  }
  .social-bar__item {
    display: flex;
    align-items: center;
    gap: 10px;
    font-weight: 600;
    font-size: 32px;
    color: var(--paper);
  }
  .social-bar__dot {
    width: 34px;
    height: 34px;
    border-radius: 50%;
    background: var(--paper);
  }
</style>
</head>
<body>
<main class="flyer">
  <svg class="flyer__shapes" viewBox="0 0 940 940" aria-hidden="false">
    <defs>
      <linearGradient id="hero-red" x1="0" y1="0" x2="1" y2="0">
        <stop offset="0" stop-color="#ec1f27"/>
        <stop offset="0.45" stop-color="#ef5057"/>
        <stop offset="0.75" stop-color="#f3a2a6"/>
        <stop offset="1" stop-color="#f4d6d8"/>
      </linearGradient>
      <linearGradient id="photo-tone" x1="0" y1="0" x2="1" y2="0">
        <stop offset="0" stop-color="#e86b71" stop-opacity="0"/>
        <stop offset="0.35" stop-color="#b8666a" stop-opacity="0.55"/>
        <stop offset="0.7" stop-color="#d9d2d3" stop-opacity="0.9"/>
        <stop offset="1" stop-color="#eeeeee"/>
      </linearGradient>
      <clipPath id="hero-clip">
        <path d="M0,178 C190,150 370,75 490,0 L940,0 L940,468 C720,458 480,495 320,540 L0,640 Z"/>
      </clipPath>
      <filter id="tag-shadow" x="-10%" y="-10%" width="130%" height="130%">
        <feDropShadow dx="4" dy="6" stdDeviation="4" flood-color="#000" flood-opacity="0.3"/>
      </filter>
    </defs>

    <!-- hero band -->
    <path d="M0,178 C190,150 370,75 490,0 L940,0 L940,468 C720,458 480,495 320,540 L0,640 Z" fill="url(#hero-red)"/>
    <g clip-path="url(#hero-clip)" role="img" aria-label="Photo of a softball player in grey uniform pants holding a glove with a ball">
      <rect x="420" y="0" width="520" height="500" fill="url(#photo-tone)"/>
    </g>

    <!-- top accent stripes -->
    <path d="M0,178 C190,150 370,75 490,0 L520,0 C400,85 200,165 0,190 Z" fill="#ec1f27"/>
    <path d="M250,118 C360,80 430,40 470,0 L500,0 C440,50 360,95 250,118 Z" fill="#fbee3e"/>

    <!-- bottom wave -->
    <path d="M0,640 L320,540 C480,495 720,458 940,468 L940,522 C760,505 520,515 312,552 L0,660 Z" fill="#fbee3e"/>
    <path d="M0,640 L320,540 C330,537 335,536 340,535 L0,655 Z" fill="#ec1f27"/>

    <!-- date tag -->
    <path d="M62,610 L312,535 L312,745 L62,745 Z" fill="#fbee3e" filter="url(#tag-shadow)"/>
  </svg>

  <div class="brand">
    <p class="brand__name">diamondscoutline.net</p>
  </div>

  <h1 class="headline">
    <span>FREE</span>
    <span>RECRUITING</span>
    <span>SEMINAR</span>
  </h1>

  <p class="event-time">
    <span>WEDNESDAY</span>
    <span class="event-time__hour">7 PM ET</span>
  </p>

  <p class="audience">Players | Parents | Coaches</p>

  <div class="web-pill">
    <svg class="web-pill__icon" viewBox="0 0 48 48" aria-hidden="true">
      <g fill="none" stroke="#ec1f27" stroke-width="3">
        <circle cx="24" cy="24" r="20"/>
        <ellipse cx="24" cy="24" rx="9" ry="20"/>
        <line x1="4" y1="24" x2="44" y2="24"/>
        <path d="M8,13 H40 M8,35 H40"/>
      </g>
    </svg>
    <span class="web-pill__url">www.diamondscoutline.net</span>
  </div>

  <footer class="social-bar">
    <span class="social-bar__item"><span class="social-bar__dot"></span>@dmndscoutline</span>
    <span class="social-bar__item"><span class="social-bar__dot"></span>@diamondscoutline</span>
    <span class="social-bar__item"><span class="social-bar__dot"></span>@dmndscoutline</span>
  </footer>
</main>
</body>
</html>
```